Business Card Design for company

We want new business cards. We'd like something different-- yet still highly professional. Our tagline is Shaping strategy, Building lasting value. Stock photos are ok, as long as they are relevant and look upscale.

Target Market(s)

Architecture/Business Management Consulting/Engineering Consulting

Contact Information for Business Card

dark gray background with pops of blue might be good, but you tell me. You're the designers. Rounded corners might be nice, but again, you tell me.

Font styles to use
Serif
Sans Serif

Colors
3276b5
5c5c5c
9d9d9d
fbfbfb

Requirements
Nice to have
• Something different, but still very professional.

```html
<!DOCTYPE html>
<html lang="en">
<head>
<meta charset="utf-8">
<title>Orven Global — Business Cards</title>
<link href="https://fonts.googleapis.com/css2?family=Montserrat:wght@400;500;600;700&family=Quicksand:wght@400;500&display=swap" rel="stylesheet">
<style>
  :root {
    --blue: #3276b5;
    --blue-soft: #5b8fcf;
    --blue-pale: #7ea7dc;
    --graphite: #4b4e55;
    --gray: #5c5c5c;
    --gray-light: #9d9d9d;
    --paper: #fbfbfb;
    --stage: #e4e5e8;
  }
  * { margin: 0; padding: 0; box-sizing: border-box; }
  html, body {
    width: 1200px; height: 900px; overflow: hidden;
    background: var(--stage);
    font-family: "Montserrat", sans-serif;
  }
  .sheet {
    position: relative; width: 1200px; height: 900px;
    display: flex; flex-direction: column; align-items: center;
    justify-content: center; gap: 40px;
  }
  .card {
    position: relative; width: 700px; height: 400px;
    border-radius: 26px; overflow: hidden;
    background: var(--paper);
    box-shadow: 0 6px 18px rgba(0,0,0,.18);
  }

  /* Front */
  .front__band {
    position: absolute; left: 0; right: 0; bottom: 0; height: 112px;
    background: var(--graphite);
    display: flex; align-items: center; justify-content: center;
  }
  .front__web {
    font-family: "Quicksand", sans-serif; color: var(--gray-light);
    font-size: 17px; letter-spacing: 5px;
  }
  .front__brand {
    position: absolute; left: 0; right: 0; top: 88px; text-align: center;
  }
  .brand-name {
    font-weight: 700; color: var(--blue); font-size: 58px; letter-spacing: 3px;
    line-height: 1; white-space: nowrap;
  }
  .tagline {
    margin-top: 20px; font-weight: 600; color: var(--blue);
    font-size: 17px; letter-spacing: .3px; white-space: nowrap;
  }

  /* Back */
  .back__art { position: absolute; inset: 0; }
  .back__brand {
    position: absolute; left: 420px; width: 270px; top: 178px; text-align: center;
  }
  .back__brand .brand-name { color: var(--paper); font-size: 28px; letter-spacing: 1.5px; }
  .person { position: absolute; left: 56px; top: 92px; }
  .person__name { font-size: 22px; color: var(--gray); font-weight: 700; letter-spacing: .5px; white-space: nowrap; }
  .person__name span { font-weight: 400; }
  .person__role {
    font-family: "Quicksand", sans-serif; font-size: 13px; color: var(--gray);
    letter-spacing: .5px; margin-top: 2px; padding-bottom: 8px;
    border-bottom: 3px solid var(--blue); width: 160px; white-space: nowrap;
  }
  .contacts { list-style: none; margin-top: 22px; display: flex; flex-direction: column; gap: 14px; }
  .contacts li { display: flex; align-items: center; gap: 14px; white-space: nowrap;
    font-family: "Quicksand", sans-serif; font-size: 17px; color: var(--gray); }
  .contacts li:nth-child(2) { margin-left: 18px; }
  .contacts li:nth-child(3) { margin-left: 36px; }
  .icon { width: 32px; height: 32px; flex: none; }
</style>
</head>
<body>
<main class="sheet">

  <section class="card front" aria-label="Card front">
    <div class="front__brand">
      <div class="brand-name">ORVEN GLOBAL</div>
      <div class="tagline">Shaping strategy, Building lasting value</div>
    </div>
    <div class="front__band">
      <span class="front__web">www.yourwebsite.com</span>
    </div>
  </section>

  <section class="card back" aria-label="Card back">
    <svg class="back__art" viewBox="0 0 700 400" width="700" height="400" aria-hidden="true">
      <polygon points="280,0 700,0 700,400 440,400 400,215" fill="var(--graphite)"/>
      <polygon points="445,0 480,0 480,112 445,88" fill="var(--blue-pale)"/>
      <polygon points="480,0 520,0 520,132 480,112" fill="var(--blue-soft)"/>
      <polygon points="400,215 440,235 470,400 440,400" fill="var(--blue-soft)"/>
      <polygon points="440,235 485,255 505,400 470,400" fill="var(--blue)"/>
    </svg>

    <div class="back__brand">
      <div class="brand-name">ORVEN GLOBAL</div>
    </div>

    <div class="person">
      <div class="person__name">YOUR <span>NAME</span></div>
      <div class="person__role">GRAPHIC DESIGNER</div>
      <ul class="contacts">
        <li>
          <svg class="icon" viewBox="0 0 32 32" aria-hidden="true">
            <circle cx="16" cy="16" r="16" fill="var(--blue)"/>
            <path d="M11 9h3l1.5 4-2 1.3a9 9 0 0 0 4.2 4.2L19 16.5l4 1.5v3c0 1-1 2-2 2A13 13 0 0 1 9 11c0-1 1-2 2-2z" fill="var(--paper)"/>
          </svg>
          000 000 0000
        </li>
        <li>
          <svg class="icon" viewBox="0 0 32 32" aria-hidden="true">
            <circle cx="16" cy="16" r="16" fill="var(--blue)"/>
            <g fill="none" stroke="var(--paper)" stroke-width="1.6">
              <circle cx="16" cy="16" r="7.5"/>
              <ellipse cx="16" cy="16" rx="3.2" ry="7.5"/>
              <line x1="8.5" y1="16" x2="23.5" y2="16"/>
            </g>
          </svg>
          youremail@xyz.com
        </li>
        <li>
          <svg class="icon" viewBox="0 0 32 32" aria-hidden="true">
            <circle cx="16" cy="16" r="16" fill="var(--blue)"/>
            <path d="M16 8a5.5 5.5 0 0 0-5.5 5.5C10.5 18 16 24 16 24s5.5-6 5.5-10.5A5.5 5.5 0 0 0 16 8z" fill="var(--paper)"/>
            <circle cx="16" cy="13.5" r="2" fill="var(--blue)"/>
          </svg>
          youraddresshere
        </li>
      </ul>
    </div>
  </section>

</main>
</body>
</html>
```